Business card for law firm

Need business card for new law firm. Think confident, authoritative, conservative, but not stuffy or old-fashioned.

Contact Information for Business Card

Content for card - logo (uploaded), plus the following:

Paul Whitcombe (larger font)
Managing Partner (larger font, but not as large as name)
Level 9, 7 Ferris Lane
Sydney NSW 2000
Main Tel 02 9364 2710
Direct Tel 02 8472 3159
Email paul@qvlegal.com.au
www.qvlegal.com.au

Letterhead design should include logo plus:
Level 9, 7 Ferris Lane
Sydney NSW 2000
Tel 02 8472 3159
www.qvlegal.com.au

```html
<!DOCTYPE html>
<html lang="en">
<head>
<meta charset="utf-8">
<title>Quayview Legal — Business Card</title>
<link href="https://fonts.googleapis.com/css2?family=Cinzel:wght@500&family=Montserrat:wght@300;400;500&family=Oswald:wght@700&display=swap" rel="stylesheet">
<style>
  :root {
    --stage: #2b2c30;
    --navy-light: #1f2a6e;
    --navy-dark: #141a4c;
    --ink: #ffffff;
    --ink-soft: #e6e8f2;
    --rule: rgba(255,255,255,0.85);
  }
  * { margin: 0; padding: 0; box-sizing: border-box; }
  html, body {
    width: 1200px; height: 900px; overflow: hidden;
    background: var(--stage);
  }
  .stage {
    width: 1200px; height: 900px;
    display: flex; flex-direction: column;
    align-items: center; justify-content: center; gap: 40px;
  }
  .card {
    position: relative;
    width: 640px; height: 391px;
    background: radial-gradient(ellipse at 35% 35%, var(--navy-light), var(--navy-dark));
    box-shadow: 0 14px 30px rgba(0,0,0,0.45);
    color: var(--ink);
  }
  /* Front: contact details */
  .identity {
    position: absolute; left: 60px; top: 122px; width: 270px;
    text-align: right;
  }
  .identity__name {
    font-family: "Oswald", sans-serif; font-weight: 700;
    font-size: 40px; line-height: 1; text-transform: uppercase;
    letter-spacing: 0.5px;
  }
  .identity__role {
    font-family: "Montserrat", sans-serif; font-weight: 300;
    font-size: 17px; margin-top: 6px; color: var(--ink-soft);
  }
  .divider {
    position: absolute; left: 350px; top: 112px;
    width: 1px; height: 118px; background: var(--rule);
  }
  .contact-list {
    position: absolute; left: 372px; top: 116px;
    list-style: none;
    font-family: "Montserrat", sans-serif; font-weight: 400;
    font-size: 16px; line-height: 27px;
  }
  .contact-list li { display: flex; align-items: center; gap: 12px; }
  .contact-list svg { width: 15px; height: 15px; flex: none; }
  .address {
    position: absolute; left: 60px; bottom: 62px;
    font-family: "Montserrat", sans-serif; font-weight: 400;
    font-size: 16px; color: var(--ink-soft);
  }
  /* Back: firm name */
  .card--back { display: flex; flex-direction: column; align-items: center; justify-content: center; }
  .wordmark { display: flex; align-items: center; gap: 16px; }
  .wordmark__dot { width: 22px; height: 22px; border-radius: 50%; background: var(--ink-soft); }
  .wordmark__name {
    font-family: "Cinzel", serif; font-weight: 500;
    font-size: 42px; letter-spacing: 3px; color: var(--ink-soft);
  }
  .website {
    margin-top: 26px;
    font-family: "Montserrat", sans-serif; font-weight: 400;
    font-size: 17px; letter-spacing: 4px; color: var(--ink-soft);
  }
</style>
</head>
<body>
<main class="stage">
  <section class="card card--front" aria-label="Business card front">
    <div class="identity">
      <h1 class="identity__name">Paul Whitcombe</h1>
      <p class="identity__role">Managing Partner</p>
    </div>
    <div class="divider"></div>
    <ul class="contact-list">
      <li>
        <svg viewBox="0 0 16 16" aria-hidden="true"><path d="M4 1.5l2.2 3-1.3 1.4c.8 1.8 2.2 3.2 4 4l1.4-1.3 3 2.2-1.2 2.4C7.6 13.7 2.3 8.4 1.6 2.7z" fill="#fff"/></svg>
        02 9364 2710
      </li>
      <li>
        <svg viewBox="0 0 16 16" aria-hidden="true"><rect x="4" y="1" width="8" height="14" rx="1.5" fill="none" stroke="#fff" stroke-width="1.5"/><circle cx="8" cy="12.3" r="0.9" fill="#fff"/></svg>
        02 8472 3159
      </li>
      <li>
        <svg viewBox="0 0 16 16" aria-hidden="true"><rect x="1.5" y="3.5" width="13" height="9" fill="none" stroke="#fff" stroke-width="1.4"/><path d="M1.5 3.5L8 9l6.5-5.5" fill="none" stroke="#fff" stroke-width="1.4"/></svg>
        paul@qvlegal.com.au
      </li>
      <li>
        <svg viewBox="0 0 16 16" aria-hidden="true"><circle cx="8" cy="8" r="6.5" fill="none" stroke="#fff" stroke-width="1.3"/><ellipse cx="8" cy="8" rx="3" ry="6.5" fill="none" stroke="#fff" stroke-width="1.1"/><path d="M1.5 8h13M2.5 4.8h11M2.5 11.2h11" stroke="#fff" stroke-width="1"/></svg>
        www.qvlegal.com.au
      </li>
    </ul>
    <p class="address">Level 9, 7 Ferris Lane Sydney NSW 2000</p>
  </section>

  <section class="card card--back" aria-label="Business card back">
    <div class="wordmark">
      <span class="wordmark__dot"></span>
      <span class="wordmark__name">Quayview Legal</span>
    </div>
    <p class="website">www.qvlegal.com.au</p>
  </section>
</main>
</body>
</html>
```